Looking for a cool & simple business-card-design for digital agency

Hi!

We are a web agency that offers Reputation Management, Vextor & Seo Services and software development. We like cool things, we like innovative styles.

We have uploaded our logo.

Project Deadline Extended Reason: Client does not want any designs with the colorful logo. Please send us submissions ONLY with the blac and white logo. What the client would like to see:1) Back of the card: is a silver logo on a black background2) front of the card with all the data, please use white background and black logo thank you Added Friday, May 8, 2015

Industry/Entity Type

Software

```html
<!DOCTYPE html>
<html lang="en">
<head>
<meta charset="utf-8">
<title>NetPerk AG – Business Card</title>
<link rel="stylesheet" href="https://fonts.googleapis.com/css2?family=Lato:wght@400;700;900&display=swap">
<style>
  :root {
    --canvas: #e9e7e4;
    --ink: #111111;
    --paper: #ffffff;
    --silver: #d9d9d9;
    --grey-pill: #a9a9a9;
    --grey-line: #a6a6a6;
    --band: #0b0b0b;
    --band-stripe: #bdbdbd;
  }
  * { box-sizing: border-box; margin: 0; padding: 0; }
  html, body { width: 1200px; height: 1000px; overflow: hidden; }
  body {
    background: var(--canvas);
    font-family: "Lato", Arial, sans-serif;
    position: relative;
  }
  .card {
    position: absolute;
    width: 620px;
    height: 354px;
    box-shadow: 0 10px 28px rgba(0,0,0,.22);
    overflow: hidden;
  }

  /* Back side */
  .card-back {
    left: 100px; top: 60px;
    background: var(--ink);
    color: var(--silver);
  }
  .card-back .brand {
    position: absolute; left: 70px; top: 118px;
    display: flex; align-items: center; gap: 18px;
  }
  .brand-square {
    width: 54px; height: 54px; background: var(--silver);
  }
  .card-back .brand-name {
    font-weight: 900; font-size: 46px; letter-spacing: 1px; color: var(--silver);
    line-height: 1;
  }
  .card-back .tagline {
    position: absolute; left: 142px; top: 172px;
    font-size: 15px; letter-spacing: 6px; text-transform: uppercase; color: var(--silver);
  }
  .card-back .services {
    position: absolute; left: 142px; top: 214px; width: 400px;
    font-size: 16px; line-height: 1.35; color: var(--silver);
  }

  /* Front side */
  .card-front {
    left: 480px; top: 520px;
    background: var(--paper);
    color: var(--ink);
  }
  .card-front .brand {
    position: absolute; left: 46px; top: 52px;
    display: flex; align-items: center; gap: 14px;
  }
  .card-front .brand-square { width: 34px; height: 34px; background: var(--ink); }
  .card-front .brand-name {
    font-weight: 900; font-size: 34px; letter-spacing: 1px; color: var(--ink); line-height: 1;
  }
  .card-front .tagline {
    position: absolute; left: 94px; top: 92px;
    font-size: 12px; letter-spacing: 5px; text-transform: uppercase; color: var(--ink);
  }
  .divider {
    position: absolute; left: 0; right: 0; top: 160px; height: 2px; background: var(--grey-line);
  }
  .name-pill {
    position: absolute; left: 150px; top: 136px;
    height: 50px; width: 330px; border-radius: 25px;
    background: var(--grey-pill);
    display: flex; align-items: center; justify-content: center; gap: 16px;
  }
  .person-name { font-weight: 900; font-size: 21px; color: var(--ink); }
  .pill-sep { width: 2px; height: 30px; background: var(--ink); }
  .person-role { font-size: 18px; color: var(--ink); }
  .contact-row {
    position: absolute; left: 36px; right: 30px; top: 232px;
    display: flex; justify-content: space-between; align-items: center;
    font-size: 17px; color: var(--ink);
  }
  .contact-item { display: flex; align-items: center; gap: 7px; }
  .contact-item svg { width: 17px; height: 17px; fill: var(--ink); }
  .band-stripe {
    position: absolute; left: 0; right: 0; bottom: 36px; height: 10px; background: var(--band-stripe);
  }
  .band {
    position: absolute; left: 0; right: 0; bottom: 0; height: 36px; background: var(--band);
  }
</style>
</head>
<body>

<section class="card card-back" aria-label="Card back">
  <div class="brand">
    <div class="brand-square"></div>
    <span class="brand-name">NetPerk AG</span>
  </div>
  <p class="tagline">Digitale Strategien</p>
  <p class="services">Reputation Management, Vextor &amp; Seo Services and Software development.</p>
</section>

<section class="card card-front" aria-label="Card front">
  <div class="brand">
    <div class="brand-square"></div>
    <span class="brand-name">NetPerk AG</span>
  </div>
  <p class="tagline">Digitale Strategien</p>

  <div class="divider"></div>
  <div class="name-pill">
    <span class="person-name">Lars Keller</span>
    <span class="pill-sep"></span>
    <span class="person-role">Director</span>
  </div>

  <div class="contact-row">
    <span class="contact-item">
      <svg viewBox="0 0 24 24" aria-hidden="true"><path d="M6.6 10.8a15.1 15.1 0 0 0 6.6 6.6l2.2-2.2a1 1 0 0 1 1-.25 11.4 11.4 0 0 0 3.6.57 1 1 0 0 1 1 1V20a1 1 0 0 1-1 1A17 17 0 0 1 3 4a1 1 0 0 1 1-1h3.5a1 1 0 0 1 1 1c0 1.25.2 2.45.57 3.57a1 1 0 0 1-.25 1z"/></svg>
      000 444 5556
    </span>
    <span class="contact-item">
      <svg viewBox="0 0 24 24" aria-hidden="true"><path d="M2 5h20v14H2zm2 2v.5l8 5 8-5V7zm0 2.8V17h16V9.8l-8 5z"/></svg>
      info@netperkag.com
    </span>
    <span class="contact-item">
      <svg viewBox="0 0 24 24" aria-hidden="true"><path d="M12 2a10 10 0 1 0 0 20 10 10 0 0 0 0-20zm6.9 6h-2.9a15 15 0 0 0-1.4-3.6A8 8 0 0 1 18.9 8zM12 4c.8 1.2 1.5 2.5 1.9 4h-3.8c.4-1.5 1.1-2.8 1.9-4zM4.3 14a8 8 0 0 1 0-4h3.4a16 16 0 0 0 0 4zm.8 2h2.9c.3 1.3.8 2.5 1.4 3.6A8 8 0 0 1 5.1 16zM8 8H5.1a8 8 0 0 1 4.3-3.6C8.8 5.5 8.3 6.7 8 8zm4 12c-.8-1.2-1.5-2.5-1.9-4h3.8c-.4 1.5-1.1 2.8-1.9 4zm2.3-6H9.7a14 14 0 0 1 0-4h4.6a14 14 0 0 1 0 4zm.3 5.6c.6-1.1 1.1-2.3 1.4-3.6h2.9a8 8 0 0 1-4.3 3.6zm1.7-5.6a16 16 0 0 0 0-4h3.4a8 8 0 0 1 0 4z"/></svg>
      www.netperkag.com
    </span>
  </div>

  <div class="band-stripe"></div>
  <div class="band"></div>
</section>

</body>
</html>
```